Business Card Update, need to bring life to the card, two sided color

We need a new business card design, are moving and changing addresses and need a new look, we have the logos already attached but need a new style moving forward. Can incorporate the color of the logo (The Green) as well, maybe a solid back? We deal with safety products revolving around static electricity and safety lighting. Would like to keep same font in second logo as well.

Target Market(s)

Electrical Safety, Lighting

Contact Information for Business Card

Dale Fenwick
Vice President
Office: 770-555-4821
Cell: 770-555-3067
dale@tkfenwick.example
www.tkfenwick.example
4700 West Harbor Boulevard
Suite #150
Roswell, GA 30076

Font styles to use
Serif
Sans Serif

Requirements
Must have
• Since 1918
Nice to have
• Could use the 100 Year Logo for back of card, would like the back of card to be the same green as logo.
Should not have
• No black cards please.

```html
<!DOCTYPE html>
<html lang="en">
<head>
<meta charset="utf-8">
<title>T.K. Fenwick Business Card</title>
<link href="https://fonts.googleapis.com/css2?family=Arimo:wght@400;700&display=swap" rel="stylesheet">
<style>
  :root {
    --brand-green: #0a9a5c;
    --paper: #ffffff;
    --ink-grey: #6f6f6f;
    --stage: #e6e8e7;
  }
  * { box-sizing: border-box; margin: 0; padding: 0; }
  html, body { width: 1200px; height: 880px; overflow: hidden; }
  body {
    background: var(--stage);
    font-family: "Arimo", Arial, sans-serif;
    position: relative;
  }
  .card {
    position: absolute;
    left: 250px;
    width: 700px;
    height: 400px;
    border-radius: 26px;
    box-shadow: 0 6px 18px rgba(0,0,0,0.18);
    overflow: hidden;
  }
  /* back side */
  .card-back { top: 20px; background: var(--brand-green); color: var(--paper); }
  .back-mark {
    position: absolute; left: 0; right: 0; top: 120px;
    display: flex; align-items: center; justify-content: center; gap: 16px;
  }
  .back-mark .dot { width: 46px; height: 46px; border-radius: 50%; background: var(--paper); }
  .back-mark .name { font-size: 34px; font-weight: 700; }
  .back-web {
    position: absolute; left: 0; right: 0; top: 250px;
    text-align: center; font-size: 22px; font-weight: 700; letter-spacing: 0.5px;
  }
  /* front side */
  .card-front { top: 460px; background: var(--paper); }
  .brand-dot {
    position: absolute; left: 40px; top: 36px;
    width: 112px; height: 112px; border-radius: 50%; background: var(--brand-green);
  }
  .company { position: absolute; left: 172px; top: 44px; color: var(--brand-green); font-weight: 700; }
  .company-name { font-size: 46px; line-height: 1; letter-spacing: -0.5px; }
  .company-sub { font-size: 22px; margin-top: 8px; }
  .company-since { font-size: 16px; font-weight: 400; color: var(--ink-grey); margin-top: 6px; letter-spacing: 1px; }
  .person { position: absolute; left: 40px; top: 184px; }
  .person-name { font-size: 30px; font-weight: 700; color: var(--brand-green); line-height: 1.1; }
  .person-role { font-size: 18px; color: var(--ink-grey); margin-top: 6px; }
  .address {
    position: absolute; right: 40px; top: 180px;
    text-align: right; font-size: 17px; color: var(--ink-grey); line-height: 24px;
  }
  .divider {
    position: absolute; left: 40px; right: 40px; top: 262px;
    height: 2px; background: var(--brand-green);
  }
  .contacts { position: absolute; left: 40px; top: 276px; list-style: none; }
  .contacts li {
    display: flex; align-items: center; gap: 12px;
    font-size: 17px; color: var(--ink-grey); line-height: 26px;
  }
  .contacts .label { color: var(--brand-green); font-weight: 700; min-width: 54px; }
  .contacts svg { width: 16px; height: 16px; flex: none; }
  .icon-fill { fill: var(--brand-green); }
  .icon-line { fill: none; stroke: var(--brand-green); stroke-width: 2; }
  .icon-cut { fill: none; stroke: var(--paper); stroke-width: 1.2; }
</style>
</head>
<body>
  <section class="card card-back" aria-label="Card back">
    <div class="back-mark">
      <span class="dot"></span>
      <span class="name">T.K. Fenwick</span>
    </div>
    <p class="back-web">www.tkfenwick.example</p>
  </section>

  <section class="card card-front" aria-label="Card front">
    <span class="brand-dot"></span>
    <div class="company">
      <p class="company-name">T.K. Fenwick</p>
      <p class="company-sub">Manufacturing Company, Inc.</p>
      <p class="company-since">Since 1918</p>
    </div>

    <div class="person">
      <p class="person-name">Dale Fenwick</p>
      <p class="person-role">Vice President</p>
    </div>

    <p class="address">4700 West Harbor Boulevard<br>Suite #150<br>Roswell, GA 30076</p>

    <div class="divider"></div>

    <ul class="contacts">
      <li>
        <svg viewBox="0 0 18 18"><rect class="icon-line" x="2" y="2" width="14" height="14"/></svg>
        <span class="label">Office</span>770-555-4821
      </li>
      <li>
        <svg viewBox="0 0 18 18"><rect class="icon-line" x="2" y="2" width="14" height="14"/></svg>
        <span class="label">Cell</span>770-555-3067
      </li>
      <li>
        <svg viewBox="0 0 18 18"><rect class="icon-fill" x="1" y="3" width="16" height="12"/><path class="icon-cut" d="M1 3 L9 10 L17 3"/></svg>
        dale@tkfenwick.example
      </li>
      <li>
        <svg viewBox="0 0 18 18"><circle class="icon-fill" cx="9" cy="9" r="8"/><path class="icon-cut" d="M1 9 H17 M9 1 V17 M3 5 H15 M3 13 H15"/><ellipse class="icon-cut" cx="9" cy="9" rx="3.5" ry="8"/></svg>
        www.tkfenwick.example
      </li>
    </ul>
  </section>
</body>
</html>
```